Need business card with a logo for a hearing aid sales and audiology business. We have two Hearing Instrument Specialists and one Audiologist on staff. Over 25 years in business. Locally owned and operated. Financing available. Most insurances accepted.

Summit Audio Wellness LLC
48730 W Larchmont, Suite 7
Spokane, WA 99281
509-617-2084
www.summitaudiowell.example

Manager
Tobias Kerrell HIS COHC
License #71829046

Target Market(s)

50yr old + people with a hearing loss.

Industry/Entity Type

Business

Contact Information for Business Card

48730 W Larchmont, Suite 7
Spokane, WA 99281
509-617-2084
www.summitaudiowell.example

Manager
Tobias Kerrell HIS COHC
NLVE #71829046

Font styles to use
Serif
Sans Serif

Requirements
Must have
• Business name, Tobias's name and title(s) and contact information, License #, web address

```html
<!DOCTYPE html>
<html lang="en">
<head>
<meta charset="utf-8">
<title>Summit Audio Wellness – Business Card</title>
<link rel="stylesheet" href="https://fonts.googleapis.com/css2?family=Josefin+Slab:wght@400;600&display=swap">
<style>
  :root {
    --backdrop: #8c8c8c;
    --card-green: #9cc33b;
    --card-black: #252324;
    --ink-dark: #2a2a28;
    --ink-light: #f4f7ec;
  }
  * { margin: 0; padding: 0; box-sizing: border-box; }
  html, body {
    width: 1200px; height: 800px; overflow: hidden;
    background: var(--backdrop);
  }
  .stage { position: relative; width: 1200px; height: 800px; }
  .business-card {
    position: absolute; left: 180px; top: 160px;
    width: 840px; height: 480px;
    border-radius: 36px; overflow: hidden;
    box-shadow: 0 18px 40px rgba(0,0,0,0.28);
    font-family: "Josefin Slab", Georgia, serif;
  }
  .card-field { position: absolute; inset: 0; }
  .holder { position: absolute; left: 62px; top: 118px; color: var(--ink-dark); }
  .holder-name { font-size: 36px; color: var(--ink-light); font-weight: 400; }
  .holder-name .credentials { font-size: 21px; margin-left: 4px; }
  .holder-role { font-size: 23px; margin-top: 2px; margin-left: 10px; }
  .holder-license { font-size: 25px; margin-top: 4px; margin-left: 20px; }
  .divider {
    position: absolute; left: 62px; top: 252px;
    width: 340px; height: 2px; background: var(--ink-dark);
  }
  .address {
    position: absolute; left: 90px; top: 286px;
    font-size: 25px; line-height: 32px; color: var(--ink-dark);
  }
  .contact-list {
    position: absolute; left: 100px; top: 372px; list-style: none;
    font-size: 26px; color: var(--ink-dark);
  }
  .contact-list li { display: flex; align-items: center; gap: 10px; height: 38px; }
  .contact-list svg { width: 26px; height: 26px; flex: none; }
  .brand {
    position: absolute; left: 600px; top: 140px; width: 220px;
    text-align: center; color: var(--ink-light);
  }
  .brand-dot {
    width: 72px; height: 72px; border-radius: 50%;
    background: var(--card-green); margin: 0 auto 26px;
  }
  .brand-name {
    font-size: 22px; font-weight: 600; letter-spacing: 3px;
    line-height: 28px; text-transform: uppercase;
  }
</style>
</head>
<body>
<main class="stage">
  <article class="business-card">
    <svg class="card-field" viewBox="0 0 840 480" preserveAspectRatio="none" aria-hidden="true">
      <rect width="840" height="480" fill="var(--card-black)"/>
      <path d="M0,0 L395,0 Q605,200 615,480 L0,480 Z" fill="var(--card-green)"/>
      <path d="M0,0 L389,0 Q599,200 609,480 L0,480 Z" fill="var(--card-black)"/>
      <path d="M0,0 L380,0 Q590,200 600,480 L0,480 Z" fill="var(--card-green)"/>
    </svg>

    <div class="holder">
      <h1 class="holder-name">Tobias Kerrell<span class="credentials">HIS COHC</span></h1>
      <p class="holder-role">Manager</p>
      <p class="holder-license">NLVE #71829046</p>
    </div>
    <div class="divider"></div>

    <address class="address">
      48730 W Larchmont, Suite 7<br>
      Spokane, WA 99281
    </address>

    <ul class="contact-list">
      <li>
        <svg viewBox="0 0 26 26" aria-hidden="true">
          <circle cx="13" cy="13" r="11.5" fill="none" stroke="var(--ink-light)" stroke-width="1.8"/>
          <path d="M9 7.5 L11 7 L12.3 10 L10.9 11.3 Q12 14 14.7 15.1 L16 13.7 L19 15 L18.5 17 Q17.5 18.6 15 18 Q9 16 8 11 Q7.5 8.5 9 7.5 Z" fill="var(--ink-light)"/>
        </svg>
        <span>509-617-2084</span>
      </li>
      <li>
        <svg viewBox="0 0 26 26" aria-hidden="true">
          <circle cx="13" cy="13" r="11.5" fill="none" stroke="var(--ink-light)" stroke-width="1.8"/>
          <ellipse cx="13" cy="13" rx="4.5" ry="11" fill="none" stroke="var(--ink-light)" stroke-width="1.4"/>
          <line x1="2" y1="13" x2="24" y2="13" stroke="var(--ink-light)" stroke-width="1.4"/>
        </svg>
        <span>www.summitaudiowell.example</span>
      </li>
    </ul>

    <div class="brand">
      <div class="brand-dot"></div>
      <p class="brand-name">Summit Audio<br>Wellness</p>
    </div>
  </article>
</main>
</body>
</html>
```